Pine Ledge Traders, LLC- Global Beverage Company with 100% Cold Chain Logistics

Hey All, My Name is Dale, I am a young business owner in a competitive export space, but my niche is that I am shipping all of my beer around the world, "100% Cold Chain". This model is more costly, but it protects the integrity of the beer itself and will give folks in foreign countries the best representation of what US Craft Beer has to offer.

I am not a branding guy and don't claim to be one, I am a salesperson first, and will be referring to all of you to create something great that will be memorable.

I am looking for a basic Business Card Design for my Craft Beer Export company. I sell US Craft Beer in several countries around the globe. Austrailia, China, Taiwan, Chile, France, New Zealand... to name a few.

I am looking for a sleek, modern, and fresh design. Quickly!

Thanks for your consideration!

Cheers,

Dale

Target Market(s)

International

Contact Information for Business Card

Dale Corrigan
Founder- Roaming Hops Guy
Dale@PineLedgeTraders.example
@RoamingHopsGuy- Instagram only
www.Pineledgetraders.example
@PineLedgeTradersAU- Instagram Only

Font styles to use
Serif

Colors
0592cd
ffffff

Requirements
Must have
• Name-
• Title-
• Email-
• Social Media Handle-
• Company Website-
Nice to have
• Nice Logo/ Images on Card
Should not have
• Tacky Beer Images

```html
<!DOCTYPE html>
<html lang="en">
<head>
<meta charset="utf-8">
<title>Pine Ledge Traders – Business Card</title>
<link rel="stylesheet" href="https://fonts.googleapis.com/css2?family=Cinzel:wght@500&family=Roboto:wght@400&display=swap">
<style>
  :root {
    --stage: #1c1c1d;
    --card: #141415;
    --brand-blue: #0592cd;
    --text-white: #ffffff;
    --text-grey: #9a9ca0;
    --silver: #c9cbcf;
    --divider: #3a3b3e;
  }
  * { margin: 0; padding: 0; box-sizing: border-box; }
  html, body {
    width: 1200px; height: 900px; overflow: hidden;
    background: var(--stage);
  }
  .sheet {
    width: 1200px; height: 900px;
    display: flex; align-items: center; justify-content: center; gap: 50px;
  }
  .card {
    width: 525px; height: 300px;
    background: var(--card);
    border-radius: 18px;
    position: relative;
    box-shadow: 0 10px 30px rgba(0,0,0,.5);
  }
  /* Front side */
  .card-front { display: flex; align-items: center; }
  .brand-block {
    width: 285px; height: 100%;
    display: flex; flex-direction: column; align-items: center; justify-content: center;
  }
  .brand-name {
    font-family: "Cinzel", serif; font-weight: 500;
    color: var(--brand-blue);
    font-size: 24px; line-height: 1.15; text-align: center;
    display: flex; align-items: center; gap: 10px;
  }
  .brand-mark {
    width: 14px; height: 14px; background: var(--brand-blue); flex: none;
  }
  .brand-tag {
    margin-top: 10px;
    font-family: "Roboto", sans-serif; font-size: 11px; letter-spacing: 2.5px;
    color: var(--text-grey); text-transform: uppercase;
  }
  .divider {
    width: 1px; height: 170px; background: var(--divider);
  }
  .contact-block {
    padding-left: 18px;
    font-family: "Roboto", sans-serif; color: var(--text-white);
  }
  .person-name {
    font-family: "Cinzel", serif; font-weight: 500;
    color: var(--brand-blue); font-size: 22px;
  }
  .person-title { font-size: 13px; margin-top: 4px; }
  .contact-list { list-style: none; margin-top: 16px; font-size: 13px; }
  .contact-list li { display: flex; align-items: center; gap: 7px; margin-bottom: 4px; }
  .contact-list li.social { margin-top: 14px; }
  .icon { width: 13px; height: 13px; flex: none; }
  /* Back side */
  .card-back {
    display: flex; flex-direction: column; align-items: center; justify-content: center;
  }
  .card-back .brand-name { color: var(--silver); font-size: 34px; }
  .card-back .brand-mark { background: var(--silver); width: 18px; height: 18px; }
  .card-back .brand-tag { color: var(--silver); font-size: 13px; margin-top: 12px; }
</style>
</head>
<body>
<main class="sheet">
  <section class="card card-front" aria-label="Card front">
    <div class="brand-block">
      <div class="brand-name"><span class="brand-mark"></span>Pine Ledge<br>Traders</div>
      <div class="brand-tag">Global Beverage Company</div>
    </div>
    <div class="divider"></div>
    <div class="contact-block">
      <div class="person-name">Dale Corrigan</div>
      <div class="person-title">Founder - Roaming Hops Guy</div>
      <ul class="contact-list">
        <li>
          <svg class="icon" viewBox="0 0 14 14" aria-hidden="true">
            <rect x="1" y="3" width="12" height="8" fill="var(--brand-blue)"/>
            <path d="M1 3 L7 8 L13 3" fill="none" stroke="var(--card)" stroke-width="1.2"/>
          </svg>
          Dale@PineLedgeTraders.example
        </li>
        <li>
          <svg class="icon" viewBox="0 0 14 14" aria-hidden="true"><circle cx="7" cy="7" r="6" fill="var(--brand-blue)"/></svg>
          www.Pineledgetraders.example
        </li>
        <li class="social">
          <svg class="icon" viewBox="0 0 14 14" aria-hidden="true"><rect x="0" y="0" width="14" height="14" fill="var(--brand-blue)"/></svg>
          @RoamingHopsGuy
        </li>
      </ul>
    </div>
  </section>

  <section class="card card-back" aria-label="Card back">
    <div class="brand-name"><span class="brand-mark"></span>Pine Ledge Traders</div>
    <div class="brand-tag">Global Beverage Company</div>
  </section>
</main>
</body>
</html>
```